Property Finance Company - Orbin Funding Limited

Background: Orbin Funding Group Limited is a private property finance company. Orbin Funding Group has capital to directly fund first mortgage, mezzanine and preferred equity financing. We also acquire performing, sub-performing and distressed debt.

Orbin Fundings management philosophy emphasises expertise, innovation, wisdom, honesty and competitiveness. Orbin Funding are not finance brokers - we provide debt funding to the commercial property and residential development sectors. Our process is built from experience and cumutavely Orbin Fundings Directors have in excess of 60 years wisdom.

The aim of the website will be to increase brand awareness, provide clients with comfort around our level of skill and background on who we are, generate more sales, and provide examples of projects that we have funded.

The website is a new product launch, and we need to use our Orbin Funding logo that has just been designed. We like a dark background, and either black/silver/grey/ jade green, or black/gold/jade green colours.

Our unique advantages are that we have fast turnaround times, we can solve clients funding problems and we know what we are doing. Our target audience will be viewing the website on both desktop and mobile devices.

We would like to have the following pages:

Home
About
Team
Services
Project Experience
Contact

Competitors Website: http://www.tarvolo.example/

We would also like to have the option of video footage in our website, as you can see in our competitors website.

Overall we want a really slick, elegant but modern website that is better than www.tarvolo.example

Target Market(s)

Finance borrowers, property developers, accountants, lawyers, businesspeople, high net worth people

Industry/Entity Type

Finance

Requirements
Must have
• Please see project description
Nice to have
Should not have

```html
<!DOCTYPE html>
<html lang="en">
<head>
<meta charset="utf-8">
<title>Orbin Funding Group</title>
<link href="https://fonts.googleapis.com/css2?family=Cinzel:wght@400;700&family=PT+Sans:wght@400;700&display=swap" rel="stylesheet">
<style>
:root{
  --green:#10a56b;
  --green-dark:#0b8a58;
  --ink:#1b1b1b;
  --text:#555;
  --rule:#e2e2e2;
  --band:#efefef;
  --footer:#070707;
  --white:#fff;
}
*{box-sizing:border-box;margin:0;padding:0}
html,body{width:1200px;height:3087px;overflow:hidden;background:var(--white)}
body{font-family:"PT Sans",Arial,sans-serif;color:var(--text);position:relative}
.abs{position:absolute}

/* hero */
.hero{left:0;top:0;width:1200px;height:640px;overflow:hidden}
.hero-photo{position:absolute;inset:0;background:
  radial-gradient(ellipse at 30% 40%,#6d5a4a 0%,transparent 55%),
  radial-gradient(ellipse at 75% 35%,#5b6670 0%,transparent 50%),
  linear-gradient(180deg,#3a3532 0%,#2a2725 60%,#1e1c1b 100%)}
.hero-shade{position:absolute;inset:0;background:rgba(20,18,17,.45)}
.hero-cut{position:absolute;left:0;top:0}
.brand{left:55px;top:14px;width:150px;text-align:center;color:var(--white);font-family:"Cinzel",Georgia,serif;white-space:nowrap}
.brand .mark{display:block;width:34px;height:34px;border-radius:50%;background:var(--white);margin:0 auto 5px}
.brand .name{display:block;font-size:15px;line-height:17px}
.brand .sub{display:block;font-size:10px;line-height:13px;letter-spacing:3px}
.nav{right:60px;top:48px;display:flex;gap:30px;font-size:16px;color:var(--white);align-items:center}
.nav .active{color:var(--green)}
.nav .active::before{content:"";display:inline-block;width:10px;height:10px;background:var(--green);border-radius:2px;margin-right:8px;transform:rotate(45deg)}
.hero-title{left:0;width:1200px;top:236px;text-align:center;color:var(--white);font-family:"Cinzel",Georgia,serif;font-size:60px;letter-spacing:1px}
.hero-sub{left:0;width:1200px;top:322px;text-align:center;color:var(--white);font-size:18px}
.play{left:550px;top:369px}

/* section headings */
.sec-head{left:78px;width:1044px;height:40px;display:flex;align-items:center;gap:34px}
.sec-head::before,.sec-head::after{content:"";flex:1;height:1px;background:var(--rule)}
.sec-head h2{font-family:"Cinzel",Georgia,serif;font-weight:400;font-size:25px;color:#333;letter-spacing:1px}

/* welcome */
.welcome h1{position:absolute;left:0;top:684px;width:1200px;text-align:center;font-family:"Cinzel",Georgia,serif;font-size:40px;color:var(--ink);font-weight:700}
.welcome p{position:absolute;left:200px;top:752px;width:800px;text-align:center;font-size:14px;line-height:31px}

/* services */
.hex{top:1054px;width:226px;height:258px}
.hex-label{position:absolute;left:0;top:0;width:226px;height:258px;display:flex;align-items:center;justify-content:center;text-align:center;font-family:"Cinzel",Georgia,serif;font-size:21px;color:#111;line-height:26px}

/* expertise */
.band{left:0;top:1412px;width:1200px;height:560px;background:var(--band)}
.exp-intro{left:78px;top:1460px;width:590px;font-size:14px;line-height:29px}
.value{left:78px;display:flex;align-items:center;gap:24px;font-family:"Cinzel",Georgia,serif;font-size:22px;color:#222}
.value .ring{width:74px;height:74px;border-radius:50%;background:var(--white);border:1px solid #ccc;display:flex;align-items:center;justify-content:center}
.value .ring.on{background:var(--green);border-color:var(--green)}

/* testimonials */
.quote{left:564px;top:2068px}
.testi{left:230px;top:2156px;width:740px;text-align:center;font-size:14px;line-height:30px}
.client{left:0;width:1200px;top:2224px;text-align:center;font-family:"Cinzel",Georgia,serif;font-size:21px;color:var(--green);font-weight:700}
.avatar{border-radius:50%;background:linear-gradient(160deg,#e9ddd3,#b9a497)}

/* projects */
.projects{left:0;top:2523px;width:1200px;height:208px;display:flex}
.projects div{flex:1;height:100%}

/* footer */
.footer{left:0;top:2731px;width:1200px;height:294px;background:var(--footer);color:var(--white)}
.f-brand{left:40px;top:36px;width:270px;text-align:center;font-family:"Cinzel",Georgia,serif;white-space:nowrap}
.f-brand .mark{display:block;width:58px;height:58px;border-radius:50%;background:var(--white);margin:0 auto 10px}
.f-brand .name{display:block;font-size:27px;line-height:30px}
.f-brand .sub{display:block;font-size:17px;line-height:22px;letter-spacing:6px}
.social{top:196px;width:36px;height:36px;border-radius:50%;border:2px solid var(--green)}
.social.fill{background:var(--green)}
.f-col h3{font-family:"Cinzel",Georgia,serif;font-weight:400;font-size:17px;letter-spacing:.5px;margin-bottom:20px}
.sitemap{left:344px;top:40px}
.sitemap li{list-style:none;font-size:13px;line-height:29px;padding-left:16px;position:relative}
.sitemap li::before{content:"";position:absolute;left:0;top:12px;width:6px;height:6px;border-radius:50%;background:var(--green)}
.contact{left:599px;top:40px;width:240px}
.c-row{position:relative;padding-left:40px;font-size:14px;line-height:24px}
.c-row svg{position:absolute;left:0;top:2px}
.c-name{color:var(--green);font-weight:700}
.news{left:873px;top:40px;width:260px}
.news p{font-size:14px;line-height:25px}
.email-box{margin-top:16px;width:251px;height:40px;background:#f2f2f2;color:#666;font-size:13px;padding:11px 12px}
.subscribe{margin-top:9px;width:166px;height:40px;background:var(--green);color:var(--white);font-family:"Cinzel",Georgia,serif;font-size:18px;text-align:center;line-height:40px;letter-spacing:1px}
.copy{left:0;top:3025px;width:1200px;height:62px;background:var(--green);color:var(--white);text-align:center;font-size:14px;line-height:62px}
</style>
</head>
<body>

<!-- hero -->
<section class="abs hero">
  <div class="hero-photo" role="img" aria-label="Team meeting around a table with laptops, dark toned"></div>
  <div class="hero-shade"></div>
  <svg class="hero-cut" width="1200" height="640" viewBox="0 0 1200 640"><polygon points="0,525 1008,638 1200,583 1200,640 0,640" fill="#fff"/></svg>
  <div class="abs brand"><span class="mark"></span><span class="name">ORBIN FUNDING</span><span class="sub">GROUP</span></div>
  <nav class="abs nav"><span class="active">HOME</span><span>ABOUT</span><span>TEAM</span><span>SERVICES</span><span>PROJECT EXPERIENCE</span><span>CONTACT</span>
    <svg width="18" height="18" viewBox="0 0 18 18"><circle cx="7.5" cy="7.5" r="5.5" fill="none" stroke="#10a56b" stroke-width="2.4"/><line x1="11.5" y1="11.5" x2="16" y2="16" stroke="#10a56b" stroke-width="2.6"/></svg>
  </nav>
  <div class="abs hero-title">ORBIN FUNDING GROUP</div>
  <div class="abs hero-sub">Orbin Funding Group has capital to directly fund first mortgage, mezzanine and preferred equity financing</div>
  <svg class="abs play" width="102" height="102" viewBox="0 0 102 102"><circle cx="51" cy="51" r="48" fill="rgba(0,0,0,.25)" stroke="#10a56b" stroke-width="4"/><polygon points="40,28 74,51 40,74" fill="#10a56b"/></svg>
</section>

<!-- welcome -->
<section class="welcome">
  <h1>WELCOME TO ORBIN FUNDING GROUP</h1>
  <p>Lorem Ipsum is simply dummy text of the printing and typesetting industry. Lorem Ipsum has been the industry's standard dummy text ever since thpe and scrambled it to make a type specimen book. It has survived not only five centuries, but also the leap into electronic typesetting, remaining essentially unchanged.</p>
  <svg class="abs" style="left:577px;top:854px" width="46" height="46" viewBox="0 0 46 46"><circle cx="23" cy="23" r="23" fill="#10a56b"/><polyline points="16,17 23,24 30,17" fill="none" stroke="#fff" stroke-width="2.4"/><polyline points="16,24 23,31 30,24" fill="none" stroke="#fff" stroke-width="2.4"/></svg>
</section>

<!-- services -->
<div class="abs sec-head" style="top:951px"><h2>SERVICES WE PROVIDE YOU</h2></div>

<div class="abs hex" style="left:76px">
  <svg width="226" height="258" viewBox="0 0 226 258" role="img" aria-label="Debt funding photo, warm office tones">
    <defs><linearGradient id="g1" x1="0" y1="0" x2="1" y2="1"><stop offset="0" stop-color="#3b3b3b"/><stop offset=".5" stop-color="#c8b7a3"/><stop offset="1" stop-color="#e09a3c"/></linearGradient></defs>
    <polygon points="113,0 226,64 226,194 113,258 0,194 0,64" fill="url(#g1)"/>
    <polygon points="113,26 203,78 203,180 113,232 23,180 23,78" fill="#10a56b" opacity=".9"/>
  </svg>
  <div class="hex-label">DEBT FUNDING</div>
</div>
<div class="abs hex" style="left:350px">
  <svg width="226" height="258" viewBox="0 0 226 258" role="img" aria-label="Mezzanine photo, warehouse shelving in grey and blue">
    <defs><linearGradient id="g2" x1="0" y1="0" x2="1" y2="1"><stop offset="0" stop-color="#2f3338"/><stop offset=".5" stop-color="#9aa6b5"/><stop offset="1" stop-color="#4a4d52"/></linearGradient></defs>
    <polygon points="113,0 226,64 226,194 113,258 0,194 0,64" fill="url(#g2)"/>
    <polygon points="113,26 203,78 203,180 113,232 23,180 23,78" fill="#fff" opacity=".72"/>
  </svg>
  <div class="hex-label">MEZZANINE</div>
</div>
<div class="abs hex" style="left:622px">
  <svg width="226" height="258" viewBox="0 0 226 258" role="img" aria-label="Equity financing photo, light interior with purple accents">
    <defs><linearGradient id="g3" x1="0" y1="0" x2="1" y2="1"><stop offset="0" stop-color="#cfcfd4"/><stop offset=".6" stop-color="#f1f1f1"/><stop offset="1" stop-color="#5a3f66"/></linearGradient></defs>
    <polygon points="113,0 226,64 226,194 113,258 0,194 0,64" fill="url(#g3)"/>
    <polygon points="113,26 203,78 203,180 113,232 23,180 23,78" fill="#fff" opacity=".72"/>
  </svg>
  <div class="hex-label">EQUITY<br>FINANCING</div>
</div>
<div class="abs hex" style="left:896px">
  <svg width="226" height="258" viewBox="0 0 226 258" role="img" aria-label="Performing photo, glass tower against teal sky">
    <defs><linearGradient id="g4" x1="0" y1="0" x2="1" y2="1"><stop offset="0" stop-color="#1d4a5c"/><stop offset=".5" stop-color="#7cb4c8"/><stop offset="1" stop-color="#123240"/></linearGradient></defs>
    <polygon points="113,0 226,64 226,194 113,258 0,194 0,64" fill="url(#g4)"/>
    <polygon points="113,26 203,78 203,180 113,232 23,180 23,78" fill="#fff" opacity=".72"/>
  </svg>
  <div class="hex-label">PERDORMING</div>
</div>

<!-- expertise -->
<div class="abs sec-head" style="top:1363px"><h2>OUR EXPERTISE</h2></div>
<div class="abs band"></div>
<p class="abs exp-intro">Lorem Ipsum is simply dummy text of the printing and typesetting industry. Lorem Ipsum has been the industry's standard dummy text ever since thpe and scrambled it to make a type specimen book. It has survived not only five centuries</p>

<div class="abs value" style="top:1566px"><span class="ring on"><svg width="34" height="34" viewBox="0 0 34 34"><circle cx="17" cy="14" r="8" fill="none" stroke="#fff" stroke-width="2"/><rect x="13" y="23" width="8" height="6" fill="none" stroke="#fff" stroke-width="2"/></svg></span>Innovation</div>
<div class="abs value" style="top:1653px"><span class="ring"><svg width="34" height="34" viewBox="0 0 34 34"><rect x="7" y="9" width="20" height="14" fill="none" stroke="#444" stroke-width="1.6"/><line x1="17" y1="23" x2="17" y2="29" stroke="#444" stroke-width="1.6"/><line x1="10" y1="29" x2="24" y2="29" stroke="#444" stroke-width="1.6"/></svg></span>Wisdom</div>
<div class="abs value" style="top:1737px"><span class="ring"><svg width="34" height="34" viewBox="0 0 34 34"><circle cx="17" cy="9" r="4.5" fill="none" stroke="#444" stroke-width="1.6"/><path d="M9 30 V19 Q17 13 25 19 V30" fill="none" stroke="#444" stroke-width="1.6"/></svg></span>Honesty</div>
<div class="abs value" style="top:1823px"><span class="ring"><svg width="34" height="34" viewBox="0 0 34 34"><circle cx="12" cy="12" r="4.5" fill="none" stroke="#444" stroke-width="1.6"/><path d="M5 27 Q12 17 19 27" fill="none" stroke="#444" stroke-width="1.6"/><circle cx="24" cy="22" r="6" fill="none" stroke="#444" stroke-width="1.6"/><line x1="24" y1="18" x2="24" y2="26" stroke="#444" stroke-width="1.6"/></svg></span>Competitiveness</div>

<svg class="abs" style="left:704px;top:1469px" width="418" height="470" viewBox="0 0 418 470" role="img" aria-label="Person silhouetted at a window overlooking city towers at dusk">
  <defs><linearGradient id="g5" x1="0" y1="0" x2="1" y2="1"><stop offset="0" stop-color="#2b3b55"/><stop offset=".45" stop-color="#c48a63"/><stop offset="1" stop-color="#1a1b22"/></linearGradient></defs>
  <polygon points="109,0 418,0 418,470 136,470 0,235" fill="url(#g5)"/>
</svg>

<!-- testimonials -->
<div class="abs sec-head" style="top:1991px"><h2>TESTIMONILAS</h2></div>
<svg class="abs quote" width="72" height="72" viewBox="0 0 72 72"><circle cx="36" cy="36" r="34" fill="none" stroke="#10a56b" stroke-width="3"/><text x="36" y="58" text-anchor="middle" font-family="Georgia,serif" font-size="52" font-weight="700" fill="#10a56b">&#8220;</text></svg>
<p class="abs testi">" Lorem Ipsum is simply dummy text of the printing and typesetting industry. Lorem Ipsum has been the industry's standard dummy text ever since the 1500s, when an unknown printer took "</p>
<div class="abs client">Client Name</div>
<svg class="abs" style="left:392px;top:2298px" width="18" height="32" viewBox="0 0 18 32"><polyline points="15,2 3,16 15,30" fill="none" stroke="#999" stroke-width="2"/></svg>
<div class="abs avatar" style="left:461px;top:2280px;width:66px;height:66px" role="img" aria-label="Client portrait"></div>
<div class="abs avatar" style="left:556px;top:2268px;width:90px;height:90px" role="img" aria-label="Client portrait"></div>
<div class="abs avatar" style="left:677px;top:2280px;width:66px;height:66px" role="img" aria-label="Client portrait"></div>
<svg class="abs" style="left:790px;top:2298px" width="18" height="32" viewBox="0 0 18 32"><polyline points="3,2 15,16 3,30" fill="none" stroke="#999" stroke-width="2"/></svg>

<!-- project experience -->
<div class="abs sec-head" style="top:2423px"><h2>PROJECT EXPERIENCE</h2></div>
<div class="abs projects">
  <div style="position:relative;background:linear-gradient(135deg,#1faa72,#0f8d5c)" role="img" aria-label="Green tinted building facade project">
    <svg style="position:absolute;left:16px;top:14px" width="208" height="180" viewBox="0 0 208 180"><rect x="1" y="1" width="206" height="178" fill="none" stroke="#fff" stroke-opacity=".6"/><circle cx="100" cy="96" r="10" fill="none" stroke="#fff" stroke-width="3"/><line x1="107" y1="103" x2="115" y2="111" stroke="#fff" stroke-width="3"/><line x1="95" y1="96" x2="105" y2="96" stroke="#fff" stroke-width="2"/><line x1="100" y1="91" x2="100" y2="101" stroke="#fff" stroke-width="2"/></svg>
  </div>
  <div style="background:linear-gradient(180deg,#6f87a3,#c9c2b5 55%,#7b746b)" role="img" aria-label="Business people walking on steps before a modern building"></div>
  <div style="background:linear-gradient(135deg,#1e3a5c,#8ea7c2 50%,#caa57d)" role="img" aria-label="Curved metal architecture"></div>
  <div style="background:linear-gradient(180deg,#8c9aa8,#3a3f47 60%,#22252b)" role="img" aria-label="Businessman in suit near office towers"></div>
  <div style="background:linear-gradient(180deg,#36566f,#b87d55 55%,#1c1e24)" role="img" aria-label="City skyline at sunset through a window"></div>
</div>

<!-- footer -->
<footer class="abs footer">
  <div class="abs f-brand"><span class="mark"></span><span class="name">ORBIN FUNDING</span><span class="sub">GROUP</span></div>
  <span class="abs social fill" style="left:142px"></span>
  <span class="abs social" style="left:186px"></span>
  <span class="abs social" style="left:229px"></span>

  <div class="abs f-col sitemap">
    <h3>SITEMAP</h3>
    <ul><li>Home</li><li>About</li><li>Team</li><li>Services</li><li>Project Experience</li><li>Contact</li></ul>
  </div>

  <div class="abs f-col contact">
    <h3>CONTACT US</h3>
    <div class="c-row"><svg width="18" height="26" viewBox="0 0 18 26"><path d="M9 1 C4 1 1 5 1 9 C1 15 9 25 9 25 C9 25 17 15 17 9 C17 5 14 1 9 1Z" fill="#10a56b"/><circle cx="9" cy="9" r="3.2" fill="#070707"/></svg><span class="c-name">ORBIN FUNDING GROUP</span><br>101 - Lorem Ipsum is simple dummy text of print text</div>
    <div class="c-row" style="margin-top:14px"><svg width="20" height="20" viewBox="0 0 20 20"><path d="M4 1 L8 1 L9 6 L6.5 8 Q8.5 12 12 13.5 L14 11 L19 12 L19 16 Q19 19 16 19 Q2 17 1 4 Q1 1 4 1Z" fill="#10a56b"/></svg>123 456 7890</div>
    <div class="c-row" style="margin-top:24px"><svg width="22" height="16" viewBox="0 0 22 16"><rect x="0" y="0" width="22" height="16" rx="1" fill="#10a56b"/><polyline points="1,1 11,9 21,1" fill="none" stroke="#070707" stroke-width="1.6"/></svg>info@orbinfundinggroup.example</div>
  </div>

  <div class="abs f-col news">
    <h3>NEWSLETTER</h3>
    <p>Would you like to receive exclusive access to articles, white papers and our regular monthly newsletter?</p>
    <div class="email-box">Enter Email *</div>
    <div class="subscribe">SUBSCRIBE</div>
  </div>
</footer>
<div class="abs copy">©ORBIN FUNDING GROUP - 2017 All Right Reserved.</div>

</body>
</html>
```